Harlow Cargomax Wrap- Pool Service Company

Looking for full vehicle wrap and half vehicle wrap designs for my swimming pool service and repair company Wren Basins LLC. Had a logo designed on here which came out great so hoping for an awesome van wrap too. I want it to have my logo in the design as well as something to do with pools and water, so you can instantly tell it is a swimming pool company at a quick glance. Plus the company information listed. This is a relatively new company so at the moment we only specialize in Pool Service and Repair, Pool Inspections, and Pool Safety Covers. I would like the design to be made so it does not focus on just listing the services allowing it to last many years as our services expand. I have attached a copy of my logo. Please let me know if anything else is needed. This will be going on a Harlow Cargomax 250 148" Medium roof van.
Target Market(s)
high income pool owners
Requirements
Must have
- Logo
Swimming pool look and feel
Pool Service and Repair, Pool Inspections, Safety Covers ...AND MORE!
555-214-8690
www.WrenBasinsQT.example
Nice to have
- Something very eye catching that grabs attention. Should be able to easily read everything without a lot of clutter or clash.

```html
<!DOCTYPE html>
<html lang="en">
<head>
<meta charset="utf-8">
<title>Wren Basins LLC – Van Wrap</title>
<link rel="stylesheet" href="https://fonts.googleapis.com/css2?family=Oswald:wght@500;700&display=swap">
<style>
  :root {
    --navy: #173f6e;
    --brand-blue: #1d4f8a;
    --orange: #e0652a;
    --water-light: #8fdcec;
    --water-mid: #3cb6d4;
    --water-deep: #1a8fb6;
    --body-white: #ffffff;
    --backdrop: #e4e4e6;
  }
  html, body {
    margin: 0;
    width: 1200px;
    height: 1167px;
    overflow: hidden;
    background: var(--backdrop);
  }
  .wrap-sheet { display: block; width: 1200px; height: 1167px; }
  .service-label { font-family: "Oswald", sans-serif; font-weight: 500; fill: #fff; font-size: 24px; }
  .brand-name { font-family: "Oswald", sans-serif; font-weight: 700; fill: var(--brand-blue); font-size: 74px; letter-spacing: 2px; }
  .phone { font-family: "Oswald", sans-serif; font-weight: 700; fill: var(--navy); font-size: 24px; }
  .web { font-family: "Oswald", sans-serif; font-weight: 500; fill: var(--orange); font-size: 14px; }
</style>
</head>
<body>
<svg class="wrap-sheet" viewBox="0 0 1200 1167" xmlns="http://www.w3.org/2000/svg">
  <defs>
    <linearGradient id="water-tone" x1="0" y1="0" x2="1" y2="1">
      <stop offset="0" stop-color="var(--water-light)"/>
      <stop offset="0.5" stop-color="var(--water-mid)"/>
      <stop offset="1" stop-color="var(--water-deep)"/>
    </linearGradient>
  </defs>

  <!-- Driver side panel -->
  <g class="side-panel side-driver">
    <rect class="panel-body" x="30" y="62" width="1135" height="410" rx="40" fill="var(--body-white)"/>
    <path role="img" aria-label="Rippling swimming pool water" d="M705 62 H1130 Q1160 62 1160 92 V385 H620 Z" fill="url(#water-tone)"/>
    <path role="img" aria-label="Pool water strip along the rocker" d="M600 440 H860 V470 H590 Z" fill="url(#water-tone)"/>
    <path class="stripe-orange" d="M680 62 H735 L650 385 H595 Z" fill="var(--orange)" opacity="0"/>
    <path class="stripe-orange" d="M680 62 H735 L718 120 H663 Z" fill="var(--orange)"/>
    <path class="stripe-navy" d="M742 62 H760 L743 120 H725 Z" fill="var(--navy)"/>
    <path class="stripe-orange" d="M590 372 H640 L625 410 H575 Z" fill="var(--orange)"/>
    <path class="stripe-orange" d="M545 440 H595 L580 470 H530 Z" fill="var(--orange)"/>
    <path class="stripe-navy" d="M602 440 H615 L600 470 H587 Z" fill="var(--navy)"/>
    <g class="service-list">
      <path d="M890 101 H1148 V135 H890 Q876 135 876 118 Q876 101 890 101 Z" fill="var(--navy)"/>
      <path d="M890 145 H1152 V179 H890 Q876 179 876 162 Q876 145 890 145 Z" fill="var(--navy)"/>
      <path d="M890 189 H1156 V223 H890 Q876 223 876 206 Q876 189 890 189 Z" fill="var(--navy)"/>
      <path d="M890 233 H1158 V267 H890 Q876 267 876 250 Q876 233 890 233 Z" fill="var(--navy)"/>
      <text class="service-label" x="895" y="127">Pool Service &amp; Repair</text>
      <text class="service-label" x="895" y="171">Pool Inspections</text>
      <text class="service-label" x="895" y="215">Safety Covers</text>
      <text class="service-label" x="895" y="259">AND MORE!</text>
    </g>
    <circle class="brand-dot" cx="720" cy="205" r="95" fill="none" stroke="var(--brand-blue)" stroke-width="12"/>
    <text class="brand-name" x="470" y="360">Wren Basins</text>
    <text class="phone" x="250" y="342">555-214-8690</text>
    <text class="web" x="250" y="360">www.WrenBasinsQT.example</text>
    <rect class="rocker" x="30" y="400" width="1135" height="36" fill="#2a2a2c"/>
  </g>

  <!-- Passenger side panel -->
  <g class="side-panel side-passenger">
    <rect class="panel-body" x="35" y="605" width="1135" height="410" rx="40" fill="var(--body-white)"/>
    <path role="img" aria-label="Rippling swimming pool water" d="M495 605 H75 Q45 605 45 635 V925 H575 Z" fill="url(#water-tone)"/>
    <path role="img" aria-label="Pool water strip along the rocker" d="M340 985 H610 V1015 H345 Z" fill="url(#water-tone)"/>
    <path class="stripe-orange" d="M462 608 H517 L532 660 H477 Z" fill="var(--orange)"/>
    <path class="stripe-navy" d="M438 608 H454 L469 660 H453 Z" fill="var(--navy)"/>
    <path class="stripe-orange" d="M580 910 H630 L645 945 H595 Z" fill="var(--orange)"/>
    <path class="stripe-orange" d="M610 985 H660 L672 1015 H622 Z" fill="var(--orange)"/>
    <path class="stripe-navy" d="M595 985 H606 L618 1015 H607 Z" fill="var(--navy)"/>
    <g class="service-list">
      <path d="M52 646 H310 Q324 646 324 663 Q324 680 310 680 H52 Z" fill="var(--navy)"/>
      <path d="M48 690 H310 Q324 690 324 707 Q324 724 310 724 H48 Z" fill="var(--navy)"/>
      <path d="M46 734 H310 Q324 734 324 751 Q324 768 310 768 H46 Z" fill="var(--navy)"/>
      <path d="M44 778 H310 Q324 778 324 795 Q324 812 310 812 H44 Z" fill="var(--navy)"/>
      <text class="service-label" x="77" y="672">Pool Service &amp; Repair</text>
      <text class="service-label" x="77" y="716">Pool Inspections</text>
      <text class="service-label" x="77" y="760">Safety Covers</text>
      <text class="service-label" x="77" y="804">AND MORE!</text>
    </g>
    <circle class="brand-dot" cx="480" cy="750" r="95" fill="none" stroke="var(--brand-blue)" stroke-width="12"/>
    <text class="brand-name" x="210" y="905">Wren Basins</text>
    <text class="phone" x="810" y="890">555-214-8690</text>
    <text class="web" x="810" y="908">www.WrenBasinsQT.example</text>
    <rect class="rocker" x="35" y="945" width="1135" height="36" fill="#2a2a2c"/>
  </g>
</svg>
</body>
</html>
```